ORLA - Óptica Médica - web design and concept

Website concept - Create and develop our website design and structure. ORLA is an optical store chain, and we are looking to establish our web and digital concept. In attachment there are several pictures about our stores and our logo.

The website structure should be user friendly. Colors should be light and the design as simple and minimalist as possible. There are different variations of the logothat can be used, check the file.

The website will include optical collections and sun collections as an online store. Also, a medical menu should be considered in order for clients to schedule optometry appointments. There should also be a menu for client assistance where the clients can read about glass maintenance in our workshop.
Updates

Low design quality

Number of Pages Required

5+ page

Font styles to use
Serif
Sans Serif

Requirements
Must have
• Must be user-friendly and minimalist.
• Please USE PICTURES FROM THE BRANDS we sell: MERUN, BOSKA, PNW, KOLE, BAMPE
Nice to have
• Nice to inspire: ZEK glasses (see website https://ch.shopzek.com/en/)
• Nice to inspire: https://merun-eyewear.com/
• Nice to ispire: https://www.pnwglobe.com/en/
Should not have
• Hysteric colors and shapes

```html
<!DOCTYPE html>
<html lang="en">
<head>
<meta charset="utf-8">
<title>ORLA – Contact Us</title>
<link href="https://fonts.googleapis.com/css2?family=Lato:wght@300;400;700&display=swap" rel="stylesheet">
<style>
:root{
  --ink:#111111;
  --text:#444444;
  --muted:#666666;
  --line:#e3e3e3;
  --accent:#e2a443;
  --footer:#000000;
  --white:#ffffff;
}
*{margin:0;padding:0;box-sizing:border-box}
html,body{width:799px;height:1200px;overflow:hidden;background:var(--white)}
body{font-family:'Lato',sans-serif;color:var(--text);position:relative}
.abs{position:absolute}
.social{display:flex;gap:6px}
.social span{width:7px;height:7px;border-radius:50%;background:var(--ink);display:block}
.brand{left:0;width:799px;top:33px;text-align:center;font-size:15px;letter-spacing:3px;color:var(--ink);font-weight:400}
.brand .mark{display:inline-block;width:6px;height:6px;background:var(--ink);margin-right:6px;vertical-align:middle}
.utility{top:11px;font-size:7px;color:var(--muted);display:flex;align-items:center;gap:4px}
.nav{top:75px;left:0;width:799px;display:flex;justify-content:center;align-items:center;gap:13px;font-size:7.5px;color:var(--text)}
.nav .active{color:var(--accent)}
.nav .cta{background:var(--ink);color:var(--white);padding:3px 4px;margin-left:1px}
.page-title{left:0;width:799px;text-align:center;font-weight:300;color:var(--ink)}
.label{font-size:7px;color:var(--muted)}
.field{border:1.5px solid var(--line);background:var(--white)}
.send{left:110px;top:716px;width:122px;height:35px;border:1.5px solid var(--ink);font-size:8.5px;color:var(--ink);display:flex;align-items:center;justify-content:center;letter-spacing:.2px}
.info h3{font-weight:300;font-size:19px;color:var(--ink);margin-bottom:8px}
.info p{font-size:7.3px;color:var(--muted);line-height:15px;padding-left:2px}
.footer{left:0;top:990px;width:799px;height:210px;background:var(--footer);color:var(--white)}
.footer .brand-f{left:108px;top:56px;font-size:12px;letter-spacing:2px;color:var(--accent)}
.footer .about{left:108px;top:79px;width:104px;font-size:7px;line-height:9px;letter-spacing:-.2px}
.footer .more{left:108px;top:112px;font-size:7px}
.footer .social{left:108px;top:130px}
.footer .social span{background:var(--white)}
.footer h4{font-size:9px;font-weight:700;letter-spacing:-.2px}
.footer ul{list-style:none;margin-top:14px}
.footer li{font-size:7px;line-height:11px;padding-left:10px;position:relative}
.footer li::before{content:"";position:absolute;left:1px;top:4.5px;width:2px;height:2px;border-radius:50%;background:var(--accent)}
.contact-row{display:flex;gap:5px;font-size:7px;line-height:11px;margin-bottom:6px}
.contact-row svg{flex:none;margin-top:2px}
.rule{left:108px;top:148px;width:586px;height:1px;background:#555}
.legal{top:160px;font-size:8.5px}
</style>
</head>
<body>

<header>
  <div class="abs social" style="left:108px;top:12px"><span></span><span></span><span></span><span></span></div>
  <div class="abs brand"><span class="mark"></span>ORLA</div>
  <div class="abs utility" style="left:547px">
    <svg width="7" height="8" viewBox="0 0 7 8"><rect x="0.5" y="3" width="6" height="5" fill="#111"/><path d="M2 3V2a1.5 1.5 0 0 1 3 0v1" stroke="#111" fill="none"/></svg>
    Your Cart&nbsp;( 0 )
  </div>
  <div class="abs utility" style="left:624px">
    <svg width="7" height="7" viewBox="0 0 10 10"><path d="M2 0l2 2.5-1 1.5a6 6 0 0 0 3 3l1.5-1L10 8 8.5 10C4 10 0 6 0 1.5z" fill="#111"/></svg>
    +012-555-214-7
  </div>
  <nav class="abs nav">
    <span>Home</span><span>Online store</span><span>Company history</span><span>Medical section</span><span>Store</span><span class="active">Contact Us</span><span class="cta">Make an Appoinment</span>
  </nav>
</header>

<main>
  <h1 class="abs page-title" style="top:136px;font-size:31px">Contact Us</h1>
  <h2 class="abs page-title" style="top:238px;font-size:31px">Send Us Your Feedback</h2>

  <form>
    <div class="abs label" style="left:109px;top:287px">Name</div>
    <div class="abs field" style="left:108px;top:301px;width:586px;height:47px"></div>
    <div class="abs label" style="left:109px;top:367px">E-Mail Address</div>
    <div class="abs field" style="left:108px;top:381px;width:586px;height:47px"></div>
    <div class="abs label" style="left:109px;top:448px">Subject</div>
    <div class="abs field" style="left:108px;top:461px;width:288px;height:47px"></div>
    <div class="abs label" style="left:405px;top:448px">Phone Number</div>
    <div class="abs field" style="left:404px;top:461px;width:288px;height:47px"></div>
    <div class="abs label" style="left:109px;top:526px">Massage</div>
    <div class="abs field" style="left:108px;top:540px;width:586px;height:149px"></div>
    <div class="abs send">SEND MASSAGE</div>
  </form>

  <section class="abs info" style="left:107px;top:840px">
    <h3>Call Us</h3>
    <p>Telephone&nbsp; : +012-555-930-4<br>Mobile&nbsp; : +012-555-930-4</p>
  </section>
  <section class="abs info" style="left:340px;top:840px">
    <h3>Mail Us</h3>
    <p style="line-height:9px">E-Mail&nbsp; : info@orlaeyecare.com</p>
  </section>
  <section class="abs info" style="left:560px;top:840px">
    <h3>Opening Hours</h3>
    <p>Monday – 3:00pm – 7:30pm<br>Tuesday – Saturday<br>10:00am – 1:00pm&nbsp;&nbsp; 3:00pm – 7:30pm<br>[Friday closed]</p>
  </section>
</main>

<footer class="abs footer">
  <div class="abs brand-f">ORLA</div>
  <p class="abs about">Lorem Ipsum is simply dummy text of the printing and typesetting industry.</p>
  <div class="abs more">READ MORE....</div>
  <div class="abs social"><span></span><span></span><span></span><span></span></div>

  <div class="abs" style="left:282px;top:58px">
    <h4>QUICK LINK</h4>
    <ul><li>Women</li><li>Men</li><li>Youth</li><li>Collections</li><li>Contact Us</li></ul>
  </div>
  <div class="abs" style="left:424px;top:58px">
    <h4>ACCOUNT</h4>
    <ul><li>My Account</li><li>My Wishlist</li><li>Checkout</li><li>Create Account</li><li>Register</li></ul>
  </div>
  <div class="abs" style="left:573px;top:58px">
    <h4>QUICK CONTACT</h4>
    <div style="margin-top:13px">
      <div class="contact-row"><svg width="6" height="6" viewBox="0 0 10 10"><path d="M2 0l2 2.5-1 1.5a6 6 0 0 0 3 3l1.5-1L10 8 8.5 10C4 10 0 6 0 1.5z" fill="#e2a443"/></svg>+012-555-214-7</div>
      <div class="contact-row"><svg width="6" height="5" viewBox="0 0 10 8"><rect width="10" height="8" fill="#e2a443"/><path d="M0 0l5 4 5-4" stroke="#000" fill="none"/></svg>info@orlaeyecare.com</div>
      <div class="contact-row"><svg width="6" height="7" viewBox="0 0 8 10"><path d="M4 0a4 4 0 0 1 4 4c0 3-4 6-4 6S0 7 0 4a4 4 0 0 1 4-4z" fill="#e2a443"/><circle cx="4" cy="4" r="1.4" fill="#000"/></svg><span>14 Birch Lane,<br>Fairview Township, NJ 07022</span></div>
    </div>
  </div>

  <div class="abs rule"></div>
  <div class="abs legal" style="left:108px">CopyRight&nbsp; ©2018 Orla Eyecare Studio. All Right Reserve</div>
  <div class="abs legal" style="right:105px">Privacy Policy - Terms &amp; Conditions</div>
</footer>

</body>
</html>
```